creation of a business card design for a company specializing in the creation...

I would like to create a design for a professional business card on a black background and with the company's colors (I am attaching some files: including the logo in horizontal and centered format, I am also attaching a recent project design a T-shirt, this is the one I chose to give you an idea of my preferences.

we are in the process of developing a new website design, it is still in the development phase but it can be viewed at the following address: www.vantrelmo.be to give you other ideas about the company
you will see for yourself the subject of my main activity: company specializing in the construction of stairs

I would like a business card that stands out from the rest with a unique design

here is the informations
Name: Lucien Barthel
Function: Manager
Address: Rue Moulinet du Parc 42
7180 La Louvière
telephone: +32 468 219 804
email: info@rx7p.be
website: rx7p. be
social networks: Facebook, YouTube, TikTok, Instagram

Target Market(s)

customer who wants to have a beautiful staircase built

Industry/Entity Type

contruction d'escalier

Contact Information for Business Card

Adresse. Numero de telephone, site web, le texte : "Createur d'escalier", logo recto-verso, icone des reseaux sociaux

Requirements
Must have
• the mention: Stair creator
Nice to have
• an illustration of a designer staircase
Should not have
• do not distort the logo

```html
<!DOCTYPE html>
<html lang="en">
<head>
<meta charset="utf-8">
<title>RX7P – Business Card</title>
<link rel="stylesheet" href="https://fonts.googleapis.com/css2?family=Montserrat:wght@300;400;500;700&display=swap">
<style>
  :root {
    --stage: #3a3b3e;
    --card: #232325;
    --brand-blue: #6f9ec2;
    --white: #f4f6f8;
  }
  * { margin: 0; padding: 0; box-sizing: border-box; }
  html, body { width: 1200px; height: 900px; overflow: hidden; }
  body {
    background: var(--stage);
    font-family: "Montserrat", sans-serif;
    display: flex;
    flex-direction: column;
    align-items: center;
    justify-content: center;
    gap: 40px;
  }
  .card {
    width: 665px;
    height: 380px;
    background: var(--card);
    border-radius: 26px;
    position: relative;
    box-shadow: 0 10px 30px rgba(0,0,0,0.35);
  }

  /* Brand name with tagline */
  .brand {
    display: flex;
    align-items: center;
    gap: 16px;
    color: var(--white);
  }
  .brand-square {
    background: var(--brand-blue);
    flex-shrink: 0;
  }
  .brand-text { display: flex; flex-direction: column; }
  .brand-name {
    font-weight: 500;
    letter-spacing: 0.12em;
    line-height: 1;
  }
  .brand-tagline {
    font-weight: 400;
    text-transform: uppercase;
    white-space: nowrap;
  }

  /* Front */
  .card-front { display: flex; align-items: center; justify-content: center; }
  .card-front .brand-name { font-size: 64px; }
  .card-front .brand-tagline { font-size: 12px; letter-spacing: 0.42em; margin-top: 10px; }
  .card-front .brand-square { width: 76px; height: 76px; }

  /* Back */
  .card-back .brand {
    position: absolute;
    top: 36px;
    left: 250px;
  }
  .card-back .brand-name { font-size: 44px; }
  .card-back .brand-tagline { font-size: 9px; letter-spacing: 0.38em; margin-top: 8px; }
  .card-back .brand-square { width: 54px; height: 54px; }

  .identity {
    position: absolute;
    top: 160px;
    left: 70px;
    width: 260px;
    text-align: right;
    color: var(--brand-blue);
  }
  .identity-name { font-size: 30px; font-weight: 700; line-height: 1.1; }
  .identity-role { font-size: 17px; font-weight: 400; margin-top: 4px; }

  .divider {
    position: absolute;
    top: 150px;
    left: 350px;
    width: 1.5px;
    height: 88px;
    background: var(--brand-blue);
  }

  .contacts {
    position: absolute;
    top: 150px;
    left: 372px;
    list-style: none;
    color: var(--brand-blue);
    font-size: 16px;
    font-weight: 400;
  }
  .contacts li { display: flex; align-items: center; gap: 12px; height: 29px; }
  .contacts svg { width: 15px; height: 15px; fill: var(--brand-blue); }

  .address {
    position: absolute;
    top: 266px;
    left: 0;
    width: 100%;
    text-align: center;
    color: var(--brand-blue);
    font-size: 17px;
    font-weight: 400;
  }

  .socials {
    position: absolute;
    bottom: 34px;
    left: 0;
    width: 100%;
    display: flex;
    justify-content: center;
    gap: 14px;
  }
  .social-dot {
    width: 20px;
    height: 20px;
    border-radius: 5px;
    background: var(--brand-blue);
  }
  .social-dot.round { border-radius: 50%; }
</style>
</head>
<body>

  <section class="card card-front">
    <div class="brand">
      <span class="brand-square"></span>
      <div class="brand-text">
        <span class="brand-name">RX7P</span>
        <span class="brand-tagline">Original Staircases</span>
      </div>
    </div>
  </section>

  <section class="card card-back">
    <div class="brand">
      <span class="brand-square"></span>
      <div class="brand-text">
        <span class="brand-name">RX7P</span>
        <span class="brand-tagline">Original Staircases</span>
      </div>
    </div>

    <div class="identity">
      <div class="identity-name">Lucien Barthel</div>
      <div class="identity-role">Manager</div>
    </div>

    <div class="divider"></div>

    <ul class="contacts">
      <li>
        <svg viewBox="0 0 24 24" aria-hidden="true"><path d="M6.6 10.8a15.1 15.1 0 0 0 6.6 6.6l2.2-2.2a1 1 0 0 1 1-.25 11.4 11.4 0 0 0 3.6.57 1 1 0 0 1 1 1V20a1 1 0 0 1-1 1A17 17 0 0 1 3 4a1 1 0 0 1 1-1h3.5a1 1 0 0 1 1 1c0 1.25.2 2.45.57 3.6a1 1 0 0 1-.25 1z"/></svg>
        +32 468 219 804
      </li>
      <li>
        <svg viewBox="0 0 24 24" aria-hidden="true"><path d="M2 5h20v14H2z M2 5l10 8 10-8" fill="none" stroke="#6f9ec2" stroke-width="2"/><path d="M3 6l9 7 9-7v-1H3z"/></svg>
        info@rx7p.be
      </li>
      <li>
        <svg viewBox="0 0 24 24" aria-hidden="true"><circle cx="12" cy="12" r="9" fill="none" stroke="#6f9ec2" stroke-width="2"/><path d="M3 12h18M12 3c3 3 3 15 0 18M12 3c-3 3-3 15 0 18" fill="none" stroke="#6f9ec2" stroke-width="1.6"/></svg>
        www.rx7p.be
      </li>
    </ul>

    <p class="address">Rue Moulinet du Parc 42 7180 La Louvière</p>

    <div class="socials" aria-label="Social networks">
      <span class="social-dot"></span>
      <span class="social-dot round"></span>
      <span class="social-dot"></span>
      <span class="social-dot"></span>
    </div>
  </section>

</body>
</html>
```